Job Recruiting Agemcy

almost like my current site www.plorvex.com but with these changes see and what i meant about the across the to the site says home job companies categories pages blog and login sign up that should only be the 4 i said only 1 home 2 industries 3 jobs 4 contact us. and remove latest blog post and our partners because that's not us we have to post acuarte information thanks and the name of the company if your using is is work and careful hiring partners and want it easy for us to post and remove jobs and where it emails us every resume or person that applies

Requirements
Must have
• must send email to us when an application is submitted and try to incorparate the colors of current site
Nice to have
• i want a pretty basic site for now just like the one i have but with all thats above were its easy for me being the own to be able to post jobs and everything

```html
<!DOCTYPE html>
<html lang="en">
<head>
<meta charset="utf-8">
<title>WCHP – Work and Careful Hiring Partners</title>
<link href="https://fonts.googleapis.com/css2?family=Lato:ital,wght@0,400;0,700;0,900;1,400&display=swap" rel="stylesheet">
<style>
:root{
  --green:#336b4c;
  --green-dark:#2b5a40;
  --pink:#cc3a60;
  --purple:#6a0fe0;
  --ink:#333;
  --muted:#f0f0f0;
  --white:#fff;
}
*{box-sizing:border-box;margin:0;padding:0}
html,body{width:1200px;height:3319px;overflow:hidden}
body{font-family:"Lato",sans-serif;color:var(--ink);position:relative;background:var(--white)}
section,header,footer{position:absolute;left:0;width:1200px}
.hex{clip-path:polygon(50% 0,100% 25%,100% 75%,50% 100%,0 75%,0 25%);position:absolute}
.btn{position:absolute;background:var(--purple);color:var(--white);font-weight:700;font-size:15px;display:flex;align-items:center;justify-content:center;letter-spacing:.3px}
.title{position:absolute;color:var(--pink);font-size:28px;font-weight:700;letter-spacing:.3px}
.title.center{left:0;width:1200px;text-align:center}
.body-text{position:absolute;font-size:14.5px;line-height:27.8px;color:#333}

/* header */
.site-header{top:0;height:122px;background:var(--green);z-index:3}
.brand{position:absolute;left:77px;top:0;width:116px;height:187px;background:var(--green-dark);display:flex;align-items:flex-end;justify-content:center;padding-bottom:42px}
.brand-name{font-size:24px;font-weight:900;color:var(--pink)}
.main-nav a{position:absolute;top:36px;height:50px;line-height:50px;color:var(--white);text-decoration:none;font-size:19px;letter-spacing:.3px}
.main-nav .active{left:356px;width:117px;text-align:center;background:var(--pink);border-radius:25px;font-weight:700}
.phone{position:absolute;left:914px;top:36px;color:var(--white)}
.phone svg{position:absolute;left:0;top:14px}
.phone .label{position:absolute;left:38px;top:2px;font-size:18px;white-space:nowrap}
.phone .number{position:absolute;left:38px;top:24px;font-size:21px;font-weight:700;white-space:nowrap}

/* hero */
.hero{top:0;height:665px;background:linear-gradient(180deg,#8a8f92 0%,#b7aea6 40%,#6f6c6c 100%)}
.hero-sub{position:absolute;top:298px;width:1200px;text-align:center;color:var(--white);font-size:31px}
.hero-title{position:absolute;top:343px;width:1200px;text-align:center;color:var(--white);font-size:43px;font-weight:900}
.search-field{position:absolute;top:420px;height:53px;background:var(--white);font-size:16px;padding-left:15px;line-height:53px;color:#333}
.search-btn{position:absolute;left:778px;top:420px;width:107px;height:53px;background:var(--pink);color:var(--white);font-weight:700;font-size:16px;line-height:53px;text-align:center}
.dots{position:absolute;display:flex;gap:9px}
.dots span{width:9px;height:9px;border-radius:50%;background:var(--white)}
.hero .dots{left:568px;top:626px}
.hero .dots span:first-child{background:#111}

/* about */
.about{top:665px;height:527px;background:var(--white)}
/* industries */
.industries{top:1192px;height:548px;background:var(--muted)}
.industry-label{position:absolute;top:396px;width:240px;text-align:center;font-size:17px;font-weight:700;line-height:26px;color:#333}
/* jobs */
.jobs{top:1740px;height:531px;background:var(--white)}
/* testimonials */
.testimonials{top:2271px;height:570px;background:var(--muted)}
.quote{position:absolute;left:120px;width:960px;top:315px;text-align:center;font-style:italic;font-size:16.5px;line-height:28px}
.person{position:absolute;width:1200px;text-align:center;font-weight:700}
.testimonials .dots{left:570px;top:488px;gap:12px}
.testimonials .dots span{width:12px;height:12px;background:#666}
.testimonials .dots span:first-child{background:#2a36e8}
/* cta */
.cta{top:2841px;height:298px;background:linear-gradient(100deg,#cc3862 0%,#8a4d5f 45%,#2f6a4a 100%);color:var(--white);text-align:center}
.cta h2{position:absolute;top:62px;width:1200px;font-size:30px;font-weight:700}
.cta p{position:absolute;top:113px;width:1200px;font-size:18px}
/* footer */
.site-footer{top:3139px;height:180px;background:var(--white);text-align:center}
.footer-nav{position:absolute;top:43px;width:1200px;display:flex;justify-content:center;gap:32px;font-weight:700;font-size:15px}
.copyright{position:absolute;top:78px;width:1200px;font-size:13px}
.social{position:absolute;top:113px;width:1200px;display:flex;justify-content:center;gap:20px}
.social span{width:22px;height:22px;border-radius:50%;background:var(--pink)}
</style>
</head>
<body>

<header class="site-header">
  <div class="brand"><span class="brand-name">WCHP</span></div>
  <nav class="main-nav">
    <a class="active" href="#">HOME</a>
    <a style="left:485px" href="#">INDUSTRIES</a>
    <a style="left:635px" href="#">JOBS</a>
    <a style="left:722px" href="#">CONTACT</a>
  </nav>
  <div class="phone">
    <svg width="24" height="24" viewBox="0 0 24 24"><path fill="#fff" d="M6.6 10.8a15.1 15.1 0 0 0 6.6 6.6l2.2-2.2a1 1 0 0 1 1-.25 11.4 11.4 0 0 0 3.6.57 1 1 0 0 1 1 1V20a1 1 0 0 1-1 1A17 17 0 0 1 3 4a1 1 0 0 1 1-1h3.5a1 1 0 0 1 1 1c0 1.25.2 2.45.57 3.57a1 1 0 0 1-.25 1z"/></svg>
    <span class="label">CALL:</span>
    <span class="number">+1 800 555 0147</span>
  </div>
</header>

<section class="hero" role="img" aria-label="Photo of a smiling team of business professionals standing together in an office">
  <div class="hero-sub">Search from 0 job offers</div>
  <h1 class="hero-title">YOUR CAREER STARTS HERE!</h1>
  <div class="search-field" style="left:315px;width:220px">Keyword</div>
  <div class="search-field" style="left:548px;width:220px">Location</div>
  <div class="search-btn">SEARCH</div>
  <div class="dots"><span></span><span></span><span></span><span></span></div>
</section>

<section class="about">
  <div class="hex" style="left:108px;top:63px;width:352px;height:406px;background:linear-gradient(135deg,#555a5e,#2f3a55)" role="img" aria-label="Photo of a smiling businessman with colleagues"></div>
  <div class="hex" style="left:322px;top:230px;width:208px;height:240px;background:#fff"></div>
  <div class="hex" style="left:328px;top:237px;width:196px;height:226px;background:linear-gradient(135deg,#d9dde2,#3b4f7a)" role="img" aria-label="Photo of two business people shaking hands"></div>
  <h2 class="title" style="left:588px;top:110px">ABOUT WCHP</h2>
  <p class="body-text" style="left:588px;top:166px;width:540px">Aliquam molestie, mi et imperdiet euismod, dui purus auctor tellus, et interdum lacus lectus et ante. Sed accumsan sollicitudin sapien, sit amet adipiscing turpis gravida ac. In congue, neque ac lobortis volutpat, libero mauris varius mi, vitae suscipit ipsum ligula vitae risus. Duis aliquam nibh a dui iaculis viverra id a velit. Vivamus egestas risus in magna varius commodo. Sed semper viverra egestas. Etiam pretium porttitor lectus, vel ornare neque porta volutpat.</p>
  <div class="btn" style="left:588px;top:360px;width:178px;height:56px">READ MORE</div>
</section>

<section class="industries">
  <h2 class="title center" style="top:68px">INDUSTRIES WE SUPPORT</h2>
  <div class="hex" style="left:97px;top:136px;width:210px;height:242px;background:linear-gradient(160deg,#4d6e86,#1d2630)" role="img" aria-label="Photo of engineers at aerospace control screens"></div>
  <div class="hex" style="left:369px;top:136px;width:210px;height:242px;background:linear-gradient(160deg,#e4e6e8,#8c9197)" role="img" aria-label="Photo of scientists working in a laboratory"></div>
  <div class="hex" style="left:640px;top:136px;width:210px;height:242px;background:linear-gradient(180deg,#4f6bb0,#e3a7b8 55%,#5d5a5e)" role="img" aria-label="Photo of a freight truck on the road at sunset"></div>
  <div class="hex" style="left:912px;top:136px;width:210px;height:242px;background:linear-gradient(160deg,#c9ccd2,#243a6e)" role="img" aria-label="Photo of a smiling medical worker in scrubs"></div>
  <div class="industry-label" style="left:82px">AERO SPACE- NORVANE AERO SYSTEMS, KESTREL ORBITAL VANTOR ELECTRIC</div>
  <div class="industry-label" style="left:354px">PHARMACEUTICAL/ HELIXA BIO LABS, MARLOW COSMETICS</div>
  <div class="industry-label" style="left:625px">TRANSPORTATION- RIDGEWAY FREIGHT, PARCELON</div>
  <div class="industry-label" style="left:897px">MEDICAL - CAREMONT, MEDVIA</div>
</section>

<section class="jobs">
  <h2 class="title" style="left:76px;top:108px">RECENT JOBS</h2>
  <p class="body-text" style="left:76px;top:164px;width:540px">Aliquam molestie, mi et imperdiet euismod, dui purus auctor tellus, et interdum lacus lectus et ante. Sed accumsan sollicitudin sapien, sit amet adipiscing turpis gravida ac. In congue, neque ac lobortis volutpat, libero mauris varius mi, vitae suscipit ipsum ligula vitae risus. Duis aliquam nibh a dui iaculis viverra id a velit. Vivamus egestas risus in magna varius commodo. Sed semper viverra egestas. Etiam pretium porttitor lectus, vel ornare neque porta volutpat.</p>
  <div class="btn" style="left:76px;top:357px;width:179px;height:56px">VIEW OPENING</div>
  <div class="hex" style="left:738px;top:60px;width:352px;height:406px;background:linear-gradient(135deg,#2a2a2a,#e9e9ec 45%,#6a6a6a)" role="img" aria-label="Photo of a laptop showing a job listings website"></div>
  <div class="hex" style="left:668px;top:232px;width:206px;height:238px;background:#fff"></div>
  <div class="hex" style="left:674px;top:239px;width:194px;height:224px;background:linear-gradient(135deg,#6b5646,#e7e1dc)" role="img" aria-label="Photo of a smiling young woman holding a document"></div>
</section>

<section class="testimonials">
  <h2 class="title center" style="top:67px">TESTIMONIALS</h2>
  <div class="hex" style="left:429px;top:148px;width:103px;height:119px;background:linear-gradient(160deg,#e8e6e4,#9a8d85)" role="img" aria-label="Portrait of a client"></div>
  <div class="hex" style="left:672px;top:148px;width:103px;height:119px;background:linear-gradient(160deg,#e8e6e4,#6e87ad)" role="img" aria-label="Portrait of a client"></div>
  <div class="hex" style="left:530px;top:131px;width:139px;height:160px;background:#fff"></div>
  <div class="hex" style="left:535px;top:137px;width:129px;height:149px;background:linear-gradient(160deg,#f1f0ee,#3d4352)" role="img" aria-label="Portrait of the featured client"></div>
  <p class="quote">“ I didn’t even need training. I couldn’t have asked for more than this. It really saves me time and effort. WCHP is exactly what our business has been lacking. I would be lost without WCHP...”</p>
  <div class="person" style="top:398px;color:var(--purple);font-size:15px">DANA WHITLOW</div>
  <div class="person" style="top:424px;font-size:15px">HR MANAGER IN BRIGHTFIELD CO.</div>
  <div class="dots"><span></span><span></span><span></span></div>
</section>

<section class="cta">
  <h2>SEEKING FOR A JOB?</h2>
  <p>Browse hundreds of job offers and find the best suitable position.</p>
  <div class="btn" style="left:409px;top:170px;width:179px;height:57px">SEARCH JOBS</div>
  <div class="btn" style="left:615px;top:170px;width:179px;height:57px">ADD A RESUME</div>
</section>

<footer class="site-footer">
  <nav class="footer-nav"><span>HOME</span><span>INDUSTRIES</span><span>JOBS</span><span>CONTACT</span></nav>
  <p class="copyright">Copyright © 2020. Company Name.All Right Reserved</p>
  <div class="social"><span></span><span></span><span></span><span></span><span></span></div>
</footer>

</body>
</html>
```